first fantastic look and impression

We are looking for a concept for letterhead, business card, emailfooter and template for invoices or offers for our company in the consultation business.
The dancer is a symbol who we are: it looks simple, but there is a lot of hard work and many years of training in this movement. The look is also what we want: elegant, modern, strong, with a touch of extravaganza
Target Market(s)
Hotelbusiness , Consulting
Font styles to use
Sans Serif
Other font styles liked:
- please give us a option we are open
Requirements
Must have
- We are not typical consultants but sparring partners and coaches for the hotel and that should also be expressed in the design. Maybe there is an icon that supports the whole thing. We are more modern and bolder than our industry colleagues.
we are modern, fresh, agile, fast
Nice to have
- a icon

```html
<!DOCTYPE html>
<html lang="de">
<head>
<meta charset="utf-8">
<title>Email Signature</title>
<link href="https://fonts.googleapis.com/css2?family=Montserrat:wght@600&family=Raleway:wght@600;700&family=Roboto:wght@400&display=swap" rel="stylesheet">
<style>
  :root {
    --page-bg: #e8e9eb;
    --card-bg: #ffffff;
    --ink: #151515;
    --navy: #1b1f2e;
    --shadow: rgba(0, 0, 0, 0.45);
  }
  html, body {
    margin: 0;
    padding: 0;
    width: 1200px;
    height: 1200px;
    overflow: hidden;
    background: var(--page-bg);
  }
  .canvas {
    position: relative;
    width: 1200px;
    height: 1200px;
  }
  .section-title {
    position: absolute;
    top: 264px;
    left: 0;
    width: 1200px;
    margin: 0;
    text-align: center;
    font-family: "Montserrat", sans-serif;
    font-weight: 600;
    font-size: 36px;
    letter-spacing: 0.5px;
    color: var(--ink);
  }
  .signature {
    position: absolute;
    left: 156px;
    width: 888px;
    background: var(--card-bg);
    box-shadow: 5px 6px 7px var(--shadow);
  }
  .signature--first { top: 366px; height: 222px; }
  .signature--second { top: 612px; height: 221px; }
  .person-name {
    position: absolute;
    left: 50px;
    margin: 0;
    font-family: "Raleway", sans-serif;
    font-weight: 700;
    font-size: 21.5px;
    letter-spacing: 0.3px;
    color: var(--navy);
    line-height: 1;
  }
  .signature--first .person-name { top: 44px; }
  .signature--second .person-name { top: 62px; }
  .name-rule {
    position: absolute;
    left: 50px;
    width: 19px;
    height: 3px;
    background: var(--navy);
  }
  .signature--first .name-rule { top: 81px; }
  .signature--second .name-rule { top: 102px; }
  .contact-item {
    position: absolute;
    display: flex;
    align-items: center;
    gap: 6px;
    font-family: "Roboto", sans-serif;
    font-size: 19px;
    color: var(--ink);
    line-height: 1;
    transform: translateY(-50%);
  }
  .contact-item svg { width: 19px; height: 19px; flex: none; }
  .col-left { left: 50px; }
  .col-right { left: 362px; }
  .brand-name {
    position: absolute;
    top: 56px;
    right: 42px;
    font-family: "Raleway", sans-serif;
    font-weight: 600;
    font-size: 22px;
    letter-spacing: 1.5px;
    color: var(--navy);
    text-transform: uppercase;
  }
</style>
</head>
<body>
<div class="canvas">
  <svg width="0" height="0" style="position:absolute">
    <defs>
      <symbol id="icon-landline" viewBox="0 0 20 20">
        <circle cx="10" cy="10" r="10" fill="#151515"/>
        <path d="M5 8.2c0-1.4 2.3-2.4 5-2.4s5 1 5 2.4v.8h-2.6v-1.2c-.8-.3-1.6-.4-2.4-.4s-1.6.1-2.4.4V9H5z M6.4 10h7.2l.9 4H5.5z" fill="#fff"/>
        <circle cx="10" cy="12" r="1.1" fill="#151515"/>
      </symbol>
      <symbol id="icon-mobile" viewBox="0 0 20 20">
        <circle cx="10" cy="10" r="10" fill="#151515"/>
        <path d="M6.6 5.2l1.8-.4 1.2 2.8-1.3 1c.6 1.3 1.6 2.3 2.9 2.9l1-1.3 2.8 1.2-.4 1.8c-.2.6-.7.9-1.3.9-4.3-.3-7.8-3.8-8.1-8.1 0-.6.3-1.1.9-1.3z" fill="#fff"/>
      </symbol>
      <symbol id="icon-mail" viewBox="0 0 20 20">
        <circle cx="10" cy="10" r="10" fill="#151515"/>
        <rect x="5" y="6.5" width="10" height="7" rx="1" fill="none" stroke="#fff" stroke-width="1.4"/>
        <path d="M5.5 7.2l4.5 3.5 4.5-3.5" fill="none" stroke="#fff" stroke-width="1.4"/>
      </symbol>
      <symbol id="icon-pin" viewBox="0 0 20 20">
        <circle cx="10" cy="10" r="10" fill="#151515"/>
        <path d="M10 4.3a4 4 0 0 0-4 4c0 3 4 7.4 4 7.4s4-4.4 4-7.4a4 4 0 0 0-4-4z" fill="#fff"/>
        <circle cx="10" cy="8.3" r="1.6" fill="#151515"/>
      </symbol>
      <symbol id="icon-globe" viewBox="0 0 20 20">
        <circle cx="10" cy="10" r="10" fill="#151515"/>
        <circle cx="10" cy="10" r="5" fill="#fff"/>
        <path d="M8 6.2c1 .8.6 1.8-.3 2.2-.9.4-.6 1.6.5 1.7 1 .1 1 1.2.4 2M12.5 6.6c-.6.9 0 1.7.9 1.6M13.8 11.5c-1 0-1.6.6-1.4 1.9" fill="none" stroke="#151515" stroke-width="1.1"/>
      </symbol>
    </defs>
  </svg>

  <h1 class="section-title">EMAIL SIGNATURE</h1>

  <section class="signature signature--first">
    <h2 class="person-name">HELENA BRANDAUER</h2>
    <div class="name-rule"></div>
    <div class="contact-item col-left" style="top:112px"><svg><use href="#icon-landline"/></svg>+43 660 4172035</div>
    <div class="contact-item col-left" style="top:140px"><svg><use href="#icon-mobile"/></svg>+43 660 5281946</div>
    <div class="contact-item col-left" style="top:169px"><svg><use href="#icon-mail"/></svg>hb@brandauerpartner.com</div>
    <div class="contact-item col-right" style="top:140px"><svg><use href="#icon-pin"/></svg>6800 Feldkirch / Markt 12</div>
    <div class="contact-item col-right" style="top:169px"><svg><use href="#icon-globe"/></svg>brandauerpartner.com</div>
    <div class="brand-name">Brandauer+Partner</div>
  </section>

  <section class="signature signature--second">
    <h2 class="person-name">JONAS BRANDAUER</h2>
    <div class="name-rule"></div>
    <div class="contact-item col-left" style="top:139px"><svg><use href="#icon-landline"/></svg>+43 660 5281946</div>
    <div class="contact-item col-left" style="top:168px"><svg><use href="#icon-mail"/></svg>jb@brandauerpartner.com</div>
    <div class="contact-item col-right" style="top:139px"><svg><use href="#icon-pin"/></svg>6800 Feldkirch / Markt 12</div>
    <div class="contact-item col-right" style="top:168px"><svg><use href="#icon-globe"/></svg>brandauerpartner.com</div>
    <div class="brand-name">Brandauer+Partner</div>
  </section>
</div>
</body>
</html>
```